Women's Health - Hormone Imbalance, Menopause, Perimenopause.

We need a poster to match a letter that will be sent out. So people see the poster in store they are reminded about the letter and the newspaper ad.
The Poster is advertising a holistic approach to treating menopause, perimenopause and women's health in general specifically hormonal imbalance.
This it the writing required on the poster
"Are you feeling out of sorts? Is your body changing? Could it be your hormones?
If you’re experiencing changes due to hormonal imbalances, it’s important to consult with a qualified medical professional who understands your needs.
Tarik Osmani, the vBlendwise Apothecary, can help. He has practiced pharmacy and nutritional medicine, helping people with hormone imbalances using a holistic approach for over 18 years.
Together, we look at issues around Hormonal Imbalance, Perimenopause and Menopause. To start, we take a profile of your sex hormones, Adrenals, Thyroids and Metabolic Pathways to see how we can best remedy the situation. Tarik uses a holistic approach that treats you as a whole – not just the symptoms – for overall better wellness.
Want to know more? Tarik is available for consultation on Wednesday Mornings at Larch Ridge Pharmacy and Thursday Mornings at Cove Brook Pharmacy.
SPECIAL OFFER! Make a booking for one session ($60) and get another session free! This limited-time package includes an initial consultation, historical hormone profile, follow-up consultation and wellness action plan.
To book an appointment with Tarik, call 1300 482 576 today."
Pictures required to correspond with the writing. I've also uploaded my logo
Industry/Entity Type
Pharmacy
Requirements
Must have
- Photos/Images to match the writing. Need women who are suffering from menopause with symptoms such as hot flashes, night sweats, anxiety, depression, fatigue, loss of libido, insomnia.
Nice to have
- Integrative Medicine, tailored medicine approach, Natural, approach, unique, tailor made solution

```html
<!DOCTYPE html>
<html lang="en">
<head>
<meta charset="utf-8">
<title>Are you feeling out of sorts? – Hormone Health Poster</title>
<link rel="stylesheet" href="https://fonts.googleapis.com/css2?family=Arvo:wght@700&family=PT+Sans:wght@400;700&family=PT+Sans+Narrow:wght@400;700&family=Open+Sans:wght@400;600;700&display=swap">
<style>
  :root{
    --orange:#ee9a1c;
    --slate:#3a3f4a;
    --slate-dark:#33373f;
    --navy:#0d4a70;
    --navy-deep:#0a3a5a;
    --red:#bf2026;
    --red-pill:#a8191f;
    --yellow:#f2e62b;
    --yellow-text:#f4d81c;
    --black:#111111;
    --white:#ffffff;
    --page:#e9e9e9;
  }
  *{margin:0;padding:0;box-sizing:border-box}
  html,body{width:1200px;height:1200px;overflow:hidden;background:var(--page)}
  .poster{
    position:absolute;left:187px;top:21px;width:826px;height:1158px;
    background:var(--white);overflow:hidden;
    font-family:"PT Sans",sans-serif;color:var(--white);
  }
  .abs{position:absolute}

  /* Headline banner */
  .headline-bubble{left:0;top:0;width:826px;height:150px}
  .headline{
    left:30px;top:35px;width:768px;height:84px;
    display:flex;align-items:center;justify-content:center;
    font-family:"Arvo",serif;font-weight:700;font-size:45px;letter-spacing:-1px;
    text-shadow:1px 2px 3px rgba(0,0,0,.35);
  }

  /* Hero */
  .hero-photo{
    left:26px;top:121px;width:385px;height:352px;
    background:linear-gradient(115deg,#8a6b55 0%,#c9b4a2 35%,#e8e1da 65%,#f4f2ef 100%);
  }
  .hero-panel{left:411px;top:121px;width:385px;height:352px;background:var(--slate)}
  .question{
    position:absolute;left:9px;width:376px;height:54px;
    background:var(--red-pill);border-radius:27px;
    display:flex;align-items:center;justify-content:center;
    font-size:30px;font-weight:400;
  }
  .question strong{color:var(--yellow-text);font-weight:700;margin:0 6px}
  .question.q1{top:17px}
  .question.q2{top:83px}
  .hero-copy{
    position:absolute;left:0;top:158px;width:385px;text-align:center;
    font-size:23px;line-height:34px;
  }
  .hero-copy .big{display:block;color:var(--yellow-text);font-weight:700;font-size:32px;line-height:36px}
  .hero-copy b{font-weight:700}

  /* Intro strip */
  .intro-strip{left:0;top:466px;width:826px;height:72px}
  .intro-text{
    left:39px;top:473px;width:747px;height:58px;
    display:flex;align-items:center;justify-content:center;text-align:center;
    font-family:"PT Sans Narrow",sans-serif;font-size:15.5px;line-height:24px;padding:0 10px;
  }
  .intro-text b{font-weight:700}

  .issues-lead{
    left:45px;top:546px;font-family:"PT Sans",sans-serif;font-weight:700;
    font-size:16px;color:var(--navy);
  }

  /* Issues band */
  .issues{left:0;top:573px;width:826px;height:255px;background:var(--navy)}
  .issue{position:absolute;top:14px;width:230px;text-align:center}
  .issue-photo{
    width:191px;height:191px;border-radius:50%;margin:0 auto;
    border:3px solid rgba(255,255,255,.85);
  }
  .issue-name{
    margin-top:12px;font-family:"Open Sans",sans-serif;font-weight:600;font-size:17px;letter-spacing:.2px;
  }
  .issue.i1{left:44px}
  .issue.i1 .issue-photo{background:radial-gradient(circle at 45% 45%,#e9cdb9,#c99a7a 55%,#efe9e4)}
  .issue.i2{left:304px}
  .issue.i2 .issue-photo{background:radial-gradient(circle at 55% 45%,#e6c6b1,#6b4836 55%,#f1eeea)}
  .issue.i3{left:559px}
  .issue.i3 .issue-photo{background:radial-gradient(circle at 45% 50%,#ecc9b0,#c8a46a 55%,#e7e1d6)}

  /* Yellow note */
  .profile-note{
    left:0;top:828px;width:826px;height:52px;background:var(--yellow);
    color:var(--black);font-family:"Open Sans",sans-serif;font-size:13.3px;line-height:18px;
    display:flex;align-items:center;justify-content:center;text-align:center;padding:0 18px;letter-spacing:-.2px;
  }
  .profile-note b{font-weight:700}

  /* Availability */
  .availability{left:0;top:880px;width:442px;height:203px;background:var(--slate)}
  .availability h2{
    font-family:"Open Sans",sans-serif;font-weight:400;font-size:25px;text-align:center;margin-top:9px;
  }
  .availability p{
    font-family:"Open Sans",sans-serif;font-size:16.5px;line-height:28px;text-align:center;margin-top:6px;padding:0 10px;
  }
  .availability .hl{color:var(--yellow-text);font-weight:700}
  .availability b{font-weight:700}
  .brand{
    position:absolute;left:6px;top:145px;width:431px;height:52px;background:var(--white);
    display:flex;align-items:center;padding-left:12px;gap:12px;
  }
  .brand-dot{width:30px;height:30px;border-radius:50%;background:var(--navy)}
  .brand-name{font-family:"PT Sans",sans-serif;font-weight:700;font-size:28px;color:var(--navy)}

  /* Offer */
  .offer{left:442px;top:880px;width:384px;height:203px;background:var(--red)}
  .offer-tab{
    position:absolute;left:6px;top:7px;width:36px;height:190px;background:var(--yellow);
  }
  .offer-tab svg{position:absolute;left:0;top:0}
  .offer-tab span{
    position:absolute;left:50%;top:50%;transform:translate(-50%,-50%) rotate(-90deg);
    white-space:nowrap;font-family:"Open Sans",sans-serif;font-weight:700;font-size:20px;color:var(--black);letter-spacing:.5px;
  }
  .offer-head{
    position:absolute;left:54px;top:12px;width:325px;
    font-family:"PT Sans Narrow",sans-serif;font-weight:700;font-size:25px;line-height:37px;letter-spacing:-.3px;
  }
  .offer-head .light{font-weight:400}
  .offer-head .free{color:var(--yellow-text)}
  .offer-body{
    position:absolute;left:50px;top:108px;width:330px;text-align:center;
    font-family:"Open Sans",sans-serif;font-size:16.5px;line-height:21px;
  }

  /* Call bar */
  .call-bar{left:0;top:1083px;width:826px;height:49px;background:var(--black)}
  .call-text{
    position:absolute;left:25px;top:0;height:49px;display:flex;align-items:center;
    font-family:"Open Sans",sans-serif;font-weight:700;font-size:22px;
  }
  .call-phone{position:absolute;left:548px;top:0;width:278px;height:49px}
  .phone-number{
    position:absolute;left:46px;top:0;height:49px;display:flex;align-items:center;
    font-family:"PT Sans",sans-serif;font-weight:700;font-size:34px;color:var(--white);
  }
</style>
</head>
<body>
<main class="poster">

  <svg class="abs headline-bubble" viewBox="0 0 826 150" aria-hidden="true">
    <path d="M72 35 H756 A42 42 0 0 1 756 119 H110 L92 141 L88 119 H72 A42 42 0 0 1 72 35 Z" fill="var(--orange)"/>
  </svg>
  <h1 class="abs headline">Are you feeling out of sorts?</h1>

  <div class="abs hero-photo" role="img" aria-label="Photo of a woman sitting on a bed, hugging her knees with her head in her hand, looking worn out"></div>

  <section class="abs hero-panel">
    <div class="question q1">Is your<strong>body changing</strong>?</div>
    <div class="question q2">Could it be your<strong>hormones</strong>?</div>
    <p class="hero-copy">
      If you’re experiencing <b>changes</b> due to
      <span class="big">hormonal imbalances,</span>
      it’s important to consult with a<br>
      <b>qualified medical professional<br>who understands your needs.</b>
    </p>
  </section>

  <svg class="abs intro-strip" viewBox="0 0 826 72" aria-hidden="true">
    <line x1="0" y1="45" x2="826" y2="45" stroke="var(--slate)" stroke-width="2"/>
    <polygon points="39,7 20,46 39,65" fill="var(--navy-deep)"/>
    <polygon points="786,7 806,46 786,65" fill="var(--navy-deep)"/>
    <rect x="39" y="7" width="747" height="58" fill="var(--navy)"/>
  </svg>
  <p class="abs intro-text">
    <span><b>Tarik Osmani</b>, the <b>vBlendwise Apothecary</b>, can help. He has practiced <b>pharmacy</b> and <b>nutritional medicine</b>,<br>
    helping people with <b>hormone imbalances</b> using a <b>holistic approach</b> for <b>over 18 years</b>.</span>
  </p>

  <p class="abs issues-lead">Together, we look at issues around</p>

  <section class="abs issues">
    <div class="issue i1">
      <div class="issue-photo" role="img" aria-label="Photo of a stressed woman holding her head in both hands"></div>
      <p class="issue-name">HORMONAL IMBALANCE</p>
    </div>
    <div class="issue i2">
      <div class="issue-photo" role="img" aria-label="Photo of a tired woman with her hand to her forehead"></div>
      <p class="issue-name">PERIMENOPAUSE</p>
    </div>
    <div class="issue i3">
      <div class="issue-photo" role="img" aria-label="Photo of a mature woman with a headache, hand at her temple"></div>
      <p class="issue-name">MENOPAUSE</p>
    </div>
  </section>

  <p class="abs profile-note">
    <span>To start, we take a profile of your <b>sex hormones</b>, <b>Adrenals</b>, <b>Thyroids</b> and <b>Metabolic Pathways</b> to see how we can best remedy<br>
    the situation. Tarik uses a holistic approach that treats you as a whole – not just the symptoms – for overall better wellness.</span>
  </p>

  <section class="abs availability">
    <h2>Want to know more?</h2>
    <p><span class="hl">Tarik</span> is available for consultation on <span class="hl">Wednesday Mornings</span> at <b>Larch Ridge Pharmacy</b> and <span class="hl">Thursday Mornings</span> at <b>Cove Brook Pharmacy</b>.</p>
    <div class="brand">
      <span class="brand-dot"></span>
      <span class="brand-name">vBlendwise Apothecary</span>
    </div>
  </section>

  <section class="abs offer">
    <div class="offer-tab">
      <svg width="48" height="190" viewBox="0 0 48 190" aria-hidden="true"><polygon points="36,14 46,24 36,34" fill="var(--yellow)"/></svg>
      <span>SPECIAL OFFER</span>
    </div>
    <p class="offer-head">BOOK FOR 1 SESSION <span class="light">( $60) &amp;</span><br>GET ANOTHER SESSION <span class="free">FREE</span></p>
    <p class="offer-body">This limited-time package includes an initial consultation, historical hormone profile, follow-up consultation and wellness action plan.</p>
  </section>

  <section class="abs call-bar">
    <p class="call-text">To book an appointment with Tarik, call today</p>
    <svg class="call-phone" viewBox="0 0 278 49" aria-hidden="true">
      <polygon points="0,49 24,0 278,0 278,49" fill="var(--orange)"/>
      <circle cx="34" cy="25" r="12" fill="none" stroke="var(--red)" stroke-width="2.5"/>
      <path d="M29 18 l3 -1 2 4 -2 2 q1 3 4 5 l2 -2 4 2 -1 3 q-3 2 -7 -1 q-5 -4 -6 -8 q0 -3 1 -4 z" fill="var(--red)"/>
    </svg>
    <p class="phone-number" style="left:594px">1300 482 576</p>
  </section>

</main>
</body>
</html>
```